Aquavelo- plumbing service flyer

Hello,
We would like to create flyer for our plumbing company Aquavelo
- we have 2 web domains
aquavelo-example.hr ( official)
preuredjenjedoma-example.hr ( for bathroom renovation)

- we would like to create a similar Z-fold flyer ( from A4 paper) for our services
- We are sending images used on our websites. Of Course, it is allowed to put some of their own. Depending on design
- sending word with text which should go on each page. Text can be modified but in the sense of a page. The massage on a page should be as in word.
What is important to us:
- to stay in blue color
- It should be 1 page when fully open. So it looks like the complete page of information
- first/front page should be with our logo and phone number. more focus on emergency plumbing.
- back page should be about bathroom remodeling. Not necessary but would be received more points
- please don't use images of regular plumbers from Pixelvault and similar. we don't want to use this stock's regular images as all others.

Target Market(s)

Bathroom remodeling and emergency plumbing

Industry/Entity Type

Construction-Plumbing

Colors
0054AA
0677BA
7BADD7
CADEEF
E8F1F8

Requirements
Must have
• Logo

```html
<!DOCTYPE html>
<html lang="en">
<head>
<meta charset="utf-8">
<title>Aquavelo – plumbing service flyer</title>
<link href="https://fonts.googleapis.com/css2?family=Montserrat:wght@300;400;500;600;700;800&display=swap" rel="stylesheet">
<style>
:root{
  --blue-deep:#0054AA;
  --blue:#0a63ae;
  --blue-mid:#0677BA;
  --blue-soft:#7BADD7;
  --blue-pale:#CADEEF;
  --blue-mist:#E8F1F8;
  --ink:#1d2430;
  --grey-row:#ececec;
  --icon-dark:#3d4148;
  --page:#ffffff;
  --stage:#eef0f3;
}
*{box-sizing:border-box;margin:0;padding:0}
html,body{width:1200px;height:3000px;overflow:hidden}
body{background:var(--stage);font-family:"Montserrat",Arial,sans-serif;color:var(--ink);position:relative}
.sheet{position:absolute;left:40px;width:1120px;height:792px;background:var(--page);box-shadow:0 10px 30px rgba(0,40,90,.18);overflow:hidden}
.sheet--outside{top:658px}
.sheet--inside{top:1550px}
.panel{position:absolute;top:0;width:373px;height:792px}
.panel--left{left:0;background:var(--blue);color:#fff}
.panel--mid{left:373px}
.panel--right{left:746px;width:374px}
.abs{position:absolute}
.art{position:absolute;border-radius:12px}
.art--light{background:linear-gradient(160deg,var(--blue-mist),var(--blue-pale))}

/* outside, left */
.brand-title{left:30px;top:48px;font-size:38px;font-weight:800;letter-spacing:1px;color:#fff}
.intro{left:30px;top:106px;width:310px;font-size:10.5px;line-height:1.35;color:#e6f0fa}
.divider{position:absolute;left:30px;width:313px;border-top:1.5px dotted rgba(255,255,255,.6)}
.offer-icon{left:30px;top:210px}
.offer-title{left:112px;top:204px;font-size:27px;font-weight:500;line-height:1}
.offer-sub{left:112px;top:232px;font-size:18px;font-weight:500}
.offer-note{left:112px;top:258px;width:220px;font-size:10px;line-height:1.3;color:#e6f0fa}
.services-lead{left:30px;top:352px;width:300px;font-size:10.5px;line-height:1.3}
.num-list{left:30px;top:400px;width:320px;list-style:none}
.num-list li{display:flex;align-items:center;height:52px}
.num-list .n{width:44px;font-size:28px;font-weight:700}
.num-list .t{font-size:10.5px;line-height:1.3}
.values{left:30px;top:690px;display:flex;gap:18px;font-size:11px;font-weight:800}
.values span::before{content:"✓ ";font-weight:700}
.slogan{left:30px;top:726px;font-size:27px;font-weight:400;letter-spacing:.5px}

/* outside, middle */
.em-title{left:148px;top:48px;line-height:1}
.em-title .a{display:block;font-size:28px;font-weight:800;color:var(--blue-deep)}
.em-title .b{display:block;font-size:33px;font-weight:800;color:var(--ink)}
.svc-title{left:26px;top:342px;font-size:26px;font-weight:700;line-height:1;color:var(--ink)}
.checks{left:26px;top:410px;width:330px;display:grid;grid-template-columns:1fr 1fr;row-gap:22px;column-gap:14px;list-style:none}
.checks li{display:flex;gap:10px;font-size:10.5px;line-height:1.25}
.checks li::before{content:"";flex:0 0 10px;height:10px;margin-top:2px;border-radius:50%;background:var(--icon-dark)}
.mid-note{left:26px;top:606px;width:300px;font-size:10.5px;line-height:1.3}
.bottom-band{position:absolute;left:373px;bottom:0;width:747px;height:100px;background:var(--blue)}
.perk{position:absolute;top:26px;display:flex;align-items:center;gap:12px;color:#fff;font-size:16px;line-height:1.1}

/* outside, right */
.logo-lockup{left:0;top:16px;width:374px;display:flex;flex-direction:column;align-items:center;gap:8px}
.logo-dot{width:84px;height:84px;border-radius:50%;background:var(--blue-mid)}
.logo-name{font-size:40px;font-weight:800;color:var(--blue-deep);letter-spacing:1px;line-height:1.1}
.feature{position:absolute;width:150px;text-align:center;font-size:10.5px;font-weight:700;line-height:1.2}
.feature .disc{display:block;width:52px;height:52px;margin:0 auto 8px;border-radius:50%;background:var(--icon-dark);border:4px solid #d9dadd}
.right-curve{position:absolute;left:0;top:0}
.phone-pill{left:24px;top:660px;width:326px;height:46px;border-radius:23px;background:#fff;display:flex;align-items:center;justify-content:center;gap:10px;font-size:27px;font-weight:700;color:var(--blue-deep)}
.contact{font-size:10px;color:#fff}

/* inside, left */
.steps-title{left:30px;top:50px;font-size:34px;font-weight:400;letter-spacing:1px}
.step{position:absolute;left:30px;width:320px;height:70px;display:flex;align-items:center}
.step .tag{position:relative;font-size:26px;font-weight:500;letter-spacing:1px}
.step .tag b{position:absolute;left:24px;top:-30px;font-size:28px;font-weight:800;line-height:1}
.step .lbl{font-size:20px;font-weight:400;line-height:1.1}

/* inside, middle */
.check-head{left:26px;top:42px;padding-left:12px;border-left:2px solid var(--blue-deep);font-size:20px;line-height:1.15;width:330px}
.check-list{left:26px;top:142px;width:320px;list-style:none}
.check-list li{display:flex;gap:16px;align-items:center;height:58px;font-size:10.5px;line-height:1.3}
.check-list .dot{flex:0 0 28px;height:28px;border-radius:50%;background:var(--ink);color:#fff;font-weight:700;font-size:15px;display:flex;align-items:center;justify-content:center}
.help-title{left:30px;top:664px;font-size:32px;font-weight:800;color:#fff;line-height:1.15}
.help-sub{left:30px;top:740px;font-size:16px;color:#fff;line-height:1.2}

/* inside, right */
.reno-head{left:30px;top:44px;font-size:21px;font-weight:700;color:var(--blue-deep);line-height:1.2}
.reno-list{left:22px;top:118px;width:316px;list-style:none}
.reno-list li{display:flex;align-items:center;height:76px;padding-left:24px;gap:40px;font-size:15px;line-height:1.2}
.reno-list li:nth-child(odd){background:var(--grey-row)}
.reno-ico{flex:0 0 42px;height:42px}
.reno-band{position:absolute;left:0;bottom:0;width:374px;height:92px;background:var(--blue);color:#fff;font-size:12px;line-height:1.25;padding:26px 30px 0}
</style>
</head>
<body>

<section class="sheet sheet--outside">
  <div class="panel panel--left">
    <h1 class="abs brand-title">AQUAVELO</h1>
    <p class="abs intro">Do you need a plumber for bathroom renovation? Did your pipe burst or have some clogging in pipes? The neighbor's has ceiling leak?</p>
    <div class="divider" style="top:176px"></div>
    <svg class="abs offer-icon" width="62" height="62" viewBox="0 0 62 62" fill="none" stroke="#fff" stroke-width="3" stroke-linecap="round" stroke-linejoin="round">
      <path d="M10 44 L30 20 L44 34 L20 54 Z"/><path d="M24 44 L34 34"/><path d="M44 12 L48 4"/><path d="M52 20 L60 16"/><path d="M50 28 L58 30"/>
    </svg>
    <div class="abs offer-title">WE OFFER</div>
    <div class="abs offer-sub">PLUMBING SERVICES</div>
    <p class="abs offer-note">in the area of the City of Zagreb and its surroundings.</p>
    <div class="divider" style="top:320px"></div>
    <p class="abs services-lead">Some of the common plumbing services include:</p>
    <ol class="abs num-list">
      <li><span class="n">1</span><span class="t">Installation of new plumbing systems</span></li>
      <li><span class="n">2</span><span class="t">Repair of leaking pipes, faucets, and fixtures</span></li>
      <li><span class="n">3</span><span class="t">Drain cleaning and unclogging</span></li>
      <li><span class="n">4</span><span class="t">Sewer line repair and replacement</span></li>
      <li><span class="n">5</span><span class="t">Bathroom and kitchen plumbing installation and repair</span></li>
    </ol>
    <div class="abs values"><span>RELIABILITY</span><span>SPEED</span><span>ACCESSIBILITY</span></div>
    <div class="abs slogan">YOUR AQUAVELO.</div>
  </div>

  <div class="panel panel--mid">
    <div class="art art--light" role="img" aria-label="Illustration of a plumber holding a wrench and a red toolbox" style="left:20px;top:40px;width:120px;height:280px"></div>
    <div class="art art--light" role="img" aria-label="Illustration of a wash basin with its drain pipe" style="left:190px;top:150px;width:130px;height:150px"></div>
    <h2 class="abs em-title"><span class="a">EMERGENCY</span><span class="b">PLUMBING</span></h2>
    <h3 class="abs svc-title">EMERGENCY<br>SERVICES:</h3>
    <ul class="abs checks">
      <li>Mechanical<br>drain cleaning</li>
      <li>Thermal imaging<br>of leakes</li>
      <li>Water jet pipe<br>cleaning</li>
      <li>main pipe<br>check up</li>
      <li>Leak detections</li>
      <li>valve change</li>
      <li>Pipe inspection<br>with camera</li>
      <li>change of<br>sink siphon</li>
    </ul>
    <p class="abs mid-note">Aquavelo team will help you to manage all the plumbing crises.</p>
  </div>

  <div class="bottom-band">
    <div class="perk" style="left:30px">
      <svg width="44" height="44" viewBox="0 0 44 44" fill="none" stroke="#fff" stroke-width="2.2" stroke-linecap="round" stroke-linejoin="round"><path d="M6 20 h10 v18 h-10z"/><path d="M16 22 l8-14 c3 0 4 2 3 6 l-1 5 h10 c2 0 3 2 2 4 l-3 12 c-1 2-2 3-4 3 h-15"/></svg>
      <span>Fast and<br>reliable</span>
    </div>
    <div class="perk" style="left:205px">
      <svg width="44" height="44" viewBox="0 0 44 44" fill="none" stroke="#fff" stroke-width="2.2"><circle cx="22" cy="22" r="17"/><path d="M34 6 l4 6 -7 1" stroke-linecap="round"/><text x="22" y="27" text-anchor="middle" font-family="Montserrat,Arial,sans-serif" font-size="13" font-weight="700" fill="#fff" stroke="none">24</text></svg>
      <span>Contact us<br>daily 24/7</span>
    </div>
  </div>

  <div class="panel panel--right">
    <div class="abs logo-lockup">
      <span class="logo-dot"></span>
      <span class="logo-name">AQUAVELO</span>
    </div>
    <div class="feature" style="left:28px;top:190px"><span class="disc"></span>BATHROOM<br>REMODELING</div>
    <div class="feature" style="left:196px;top:190px"><span class="disc"></span>EMERGENCY<br>PLUMBING</div>
    <div class="feature" style="left:28px;top:306px"><span class="disc"></span>PLUMBING</div>
    <div class="feature" style="left:196px;top:306px"><span class="disc"></span>LEK DETECTION</div>
    <svg class="right-curve" width="374" height="792" viewBox="0 0 374 792">
      <path d="M0 640 C30 560 110 520 200 505 C270 495 330 470 374 440 V792 H0 Z" fill="var(--blue)"/>
    </svg>
    <div class="art" role="img" aria-label="Illustration of a masked plumber hero mascot holding a pipe" style="left:96px;top:428px;width:180px;height:220px;background:linear-gradient(180deg,var(--blue-soft),var(--blue-mid))"></div>
    <div class="abs phone-pill">
      <svg width="22" height="22" viewBox="0 0 24 24" fill="none" stroke="var(--blue-deep)" stroke-width="2" stroke-linejoin="round"><path d="M5 3 h4 l2 5 -2.5 1.5 a11 11 0 0 0 6 6 L16 13 l5 2 v4 a2 2 0 0 1-2 2 A16 16 0 0 1 3 5 a2 2 0 0 1 2-2z"/></svg>
      +385 91 000 4821
    </div>
    <div class="abs contact" style="left:30px;top:720px">✉ info@aquavelo-example.hr</div>
    <div class="abs contact" style="left:200px;top:720px">⊕ www.aquavelo-example.com</div>
    <div class="abs contact" style="left:70px;top:754px">⊕ www.preuredjenjedoma-example.hr</div>
  </div>
</section>

<section class="sheet sheet--inside">
  <div class="panel panel--left">
    <h2 class="abs steps-title">PLUMBING STEPS:</h2>
    <div class="step" style="top:126px"><span class="tag">STEP<b>1</b></span><span class="lbl" style="margin-left:50px">Planning<br>faze</span></div>
    <div class="step" style="top:206px"><span class="lbl" style="margin-left:8px;width:150px">Demolition</span><span class="tag">STEP<b>2</b></span></div>
    <div class="step" style="top:292px"><span class="tag">STEP<b>3</b></span><span class="lbl" style="margin-left:50px">Ceramic work</span></div>
    <div class="step" style="top:380px"><span class="lbl" style="margin-left:8px;width:150px">Electric work</span><span class="tag">STEP<b>4</b></span></div>
    <div class="step" style="top:466px"><span class="tag">STEP<b>5</b></span><span class="lbl" style="margin-left:50px">Plumbing faze</span></div>
    <div class="step" style="top:560px"><span class="lbl" style="margin-left:8px;width:150px">Final sanitary<br>installation</span><span class="tag">STEP<b>6</b></span></div>
    <div class="step" style="top:660px"><span class="tag">STEP<b>7</b></span><span class="lbl" style="margin-left:50px">Final cleaning</span></div>
  </div>

  <div class="panel panel--mid">
    <p class="abs check-head">What to check before installation and putting tiles on walls.</p>
    <ol class="abs check-list">
      <li><span class="dot">1</span>Decide on type of pipes: PEX, PPR, Inox</li>
      <li><span class="dot">2</span>Inspect pipes with camera to check is pipe fall ok</li>
      <li><span class="dot">3</span>Test water pipes with test pump</li>
      <li><span class="dot">4</span>Take images of each wall with install pipes on it before closing.</li>
    </ol>
    <div class="art art--light" role="img" aria-label="Illustration of a plumber surrounded by pipes, wrenches and plumbing tools" style="left:40px;top:390px;width:270px;height:230px;border-radius:50% 50% 8px 8px"></div>
    <svg class="abs" style="left:0;top:0" width="373" height="792" viewBox="0 0 373 792">
      <path d="M0 630 C90 590 170 600 230 640 C280 675 320 690 373 690 V792 H0 Z" fill="var(--blue)"/>
    </svg>
    <h3 class="abs help-title">This steps<br>will help you</h3>
    <p class="abs help-sub">to be sure that installations<br>are ok before closing.</p>
  </div>

  <div class="panel panel--right">
    <h2 class="abs reno-head">Steps for renovating a<br>bathroom:</h2>
    <ul class="abs reno-list">
      <li><svg class="reno-ico" viewBox="0 0 42 42" fill="none" stroke="var(--blue-deep)" stroke-width="2"><rect x="6" y="16" width="30" height="20" rx="3"/><text x="21" y="31" text-anchor="middle" font-family="Montserrat,Arial,sans-serif" font-size="12" font-weight="700" fill="var(--blue-deep)" stroke="none">$</text><path d="M14 16 V9 h14 v7"/></svg>Plan your<br>budget</li>
      <li><svg class="reno-ico" viewBox="0 0 42 42" fill="none" stroke="var(--blue-deep)" stroke-width="2"><circle cx="21" cy="21" r="12"/><path d="M21 3 v6 M21 33 v6 M3 21 h6 M33 21 h6"/><circle cx="21" cy="21" r="4"/></svg>Plan your<br>design</li>
      <li><svg class="reno-ico" viewBox="0 0 42 42" fill="none" stroke="var(--blue-deep)" stroke-width="2"><circle cx="21" cy="13" r="7"/><path d="M8 38 c0-9 6-14 13-14 s13 5 13 14"/></svg>Hire a<br>professionals</li>
      <li><svg class="reno-ico" viewBox="0 0 42 42" fill="none" stroke="var(--blue-deep)" stroke-width="2"><path d="M8 18 h26 c0 9-6 14-13 14 S8 27 8 18z"/><path d="M21 32 v6 M14 38 h14 M21 18 V8 h6"/></svg>Decide about<br>sanitary ware</li>
      <li><svg class="reno-ico" viewBox="0 0 42 42" fill="none" stroke="var(--blue-deep)" stroke-width="2"><rect x="6" y="6" width="14" height="10" rx="2"/><path d="M20 11 h8 l4 8 M13 16 v20"/><path d="M30 22 l6 6 M34 20 l4 4"/></svg>Choose tile<br>and paint</li>
      <li><svg class="reno-ico" viewBox="0 0 42 42" fill="none" stroke="var(--blue-deep)" stroke-width="2"><ellipse cx="14" cy="14" rx="8" ry="10"/><path d="M26 8 h10 v12 h-10z M14 24 v14 M26 30 h10"/></svg>Install bathroom<br>accessories</li>
      <li><svg class="reno-ico" viewBox="0 0 42 42" fill="none" stroke="var(--blue-deep)" stroke-width="2"><path d="M12 6 h14 v8 h-14z M14 14 l-4 22 h18 l-2-22"/><circle cx="32" cy="10" r="2"/><circle cx="36" cy="16" r="1.5"/></svg>Clean up</li>
    </ul>
    <p class="reno-band">By following these steps, you can successfully renovate your bathroom and create a space that meets your needs and style preferences.</p>
  </div>
</section>

</body>
</html>
```